Redesign Of Current Landing Page

I need to redesign this landing page https://www.brightlanepromo.biz/?page=landing&landing=23 (Please do not opt in because when you do it will show you the home page. Please clear your cookies before going to this url above to view the 1 page landing page.)

Please use my updated website as a reference for colors and logo.
http://sitecradlewerk.com/dh/bpq/index.html

I would like the call to action to be a button that opens into a lead form...

Button would be "Download Samples"

Target Market(s)

small business owners

Industry/Entity Type

Marketing

Number of Pages Required

1 page

Colors

Designer to choose colors to be used in the design.

Requirements
Must have
• must be full responsive on all devices
Nice to have
• must have a legitimate professional apeal to it
Should not have
• open

```html
<!DOCTYPE html>
<html lang="en">
<head>
<meta charset="utf-8">
<title>Brightlane Promo Group — Attract More Customers</title>
<link rel="stylesheet" href="https://fonts.googleapis.com/css2?family=Lato:wght@400;700;900&display=swap">
<style>
:root{
  --blue:#1b72c4;
  --orange:#fba31b;
  --ink:#2b2b2b;
  --light:#f2f2f2;
  --grey:#ececec;
  --footer:#d4d4d4;
  --white:#fff;
}
*{box-sizing:border-box;margin:0;padding:0}
html,body{width:1200px;height:3025px;overflow:hidden}
body{font-family:"Lato",Arial,sans-serif;color:var(--ink);background:var(--white);position:relative}
.section{position:absolute;left:0;width:1200px}
.btn{position:absolute;display:flex;align-items:center;justify-content:center;background:var(--orange);color:#1f1f1f;font-weight:700;font-size:17px;letter-spacing:.2px;text-transform:uppercase;text-decoration:none;white-space:nowrap}
.btn--center{left:377px;width:446px;height:56px}

/* hero */
.hero{top:0;height:665px;background:linear-gradient(180deg,#4e6fae 0%,#8d7fa6 28%,#e6a05e 45%,#c79a9c 62%,#b5a6c6 80%,#9a8fb8 100%)}
.hero__brand{position:absolute;left:136px;top:38px;display:flex;align-items:center;gap:10px;color:var(--white);font-weight:900;font-size:30px;letter-spacing:1px}
.hero__brand-dot{width:30px;height:30px;border-radius:50%;background:var(--blue)}
.hero__contact{position:absolute;top:20px;display:flex;align-items:center;gap:10px;font-weight:700;font-size:17px;color:#1a1a1a}
.hero__icon{width:24px;height:24px;border-radius:50%;background:var(--orange);display:flex;align-items:center;justify-content:center}
.hero__panel{position:absolute;left:318px;top:184px;width:554px;height:352px;background:rgba(60,60,60,.72);border:1px solid rgba(255,255,255,.25);text-align:center;color:var(--white)}
.hero__title{font-weight:900;font-size:38px;line-height:45px;margin-top:34px;text-transform:uppercase}
.hero__sub{font-size:21px;line-height:26px;margin-top:10px}
.hero__note{font-size:15px;line-height:20px;margin-top:18px}
.hero__panel .btn{left:48px;top:260px;width:458px;height:56px}

/* imagine */
.imagine{top:665px;height:602px;background:var(--light)}
.heading{font-weight:900;color:var(--blue);font-size:31px;text-transform:uppercase}
.imagine .heading{position:absolute;left:131px;top:57px}
.imagine__card{position:absolute;left:131px;top:122px;width:797px;height:302px;background:var(--light);border:2px solid #e2e2e2;padding:38px 300px 0 40px;font-size:14.5px;line-height:21px;color:#333}
.imagine__card p+p{margin-top:18px}
.imagine__art{position:absolute;left:640px;top:165px;width:430px;height:295px;border-radius:4px;background:linear-gradient(135deg,#e4e4e4 0%,#c9c9c9 40%,#d9a5a5 65%,#c93a3a 100%)}
.imagine .btn{left:131px;top:455px;width:444px;height:56px}

/* how */
.how{top:1267px;height:468px;background:linear-gradient(180deg,#2e86c9 0%,#1c78c6 45%,#1d84d2 100%);text-align:center;color:var(--white)}
.how__title{position:absolute;left:0;width:1200px;top:58px;font-weight:900;font-size:30px;color:var(--orange);text-transform:uppercase}
.how__text{position:absolute;left:245px;width:710px;font-size:14.5px;line-height:22px}
.how .btn{top:347px}

/* why */
.why{top:1735px;height:645px;background:var(--white);text-align:center}
.why .heading{position:absolute;left:0;width:1200px;top:86px;line-height:42px}
.benefit{position:absolute;top:232px;width:170px;margin-left:-85px;text-align:center}
.benefit__ring{width:133px;height:133px;margin:0 auto;border:2px solid var(--blue);border-radius:50%;display:flex;align-items:center;justify-content:center}
.benefit__label{margin-top:44px;font-size:12.5px;line-height:18px;color:#222}
.why .btn{top:500px}

/* testimonials */
.testimonials{top:2380px;height:581px;background:var(--grey);text-align:center}
.testimonials .heading{position:absolute;left:0;width:1200px;top:77px}
.quote{position:absolute;left:324px;width:552px;top:135px;font-size:14.5px;line-height:26px;color:#444}
.quote__mark{position:absolute;font-family:Georgia,serif;font-weight:700;font-size:70px;color:#333;line-height:1}
.quote__name{position:absolute;left:0;width:1200px;top:370px;font-size:12px;font-weight:700;color:var(--blue)}
.quote__place{position:absolute;left:0;width:1200px;top:388px;font-size:12px;color:#555}
.testimonials .btn{top:454px}

/* footer */
.footer{top:2961px;height:64px;background:var(--footer);display:flex;align-items:center;justify-content:center;font-size:11px;color:#555}
</style>
</head>
<body>

<header class="section hero" role="img" aria-label="Airplane wing flying above sunset clouds">
  <div class="hero__brand"><span class="hero__brand-dot"></span>BLPG</div>
  <div class="hero__contact" style="left:680px">
    <span class="hero__icon"><svg width="12" height="12" viewBox="0 0 24 24"><path d="M6.6 10.8a15 15 0 006.6 6.6l2.2-2.2c.3-.3.7-.4 1-.2 1.1.4 2.3.6 3.6.6.6 0 1 .4 1 1V20c0 .6-.4 1-1 1A17 17 0 013 4c0-.6.4-1 1-1h3.5c.6 0 1 .4 1 1 0 1.3.2 2.5.6 3.6.1.3 0 .7-.2 1z" fill="#1a1a1a"/></svg></span>1-800-555-0142
  </div>
  <div class="hero__contact" style="left:858px">
    <span class="hero__icon"><svg width="12" height="12" viewBox="0 0 24 24"><circle cx="12" cy="12" r="9" fill="none" stroke="#1a1a1a" stroke-width="3"/><path d="M12 7v5l3 2" stroke="#1a1a1a" stroke-width="3" fill="none"/></svg></span>MON-FRI 8AM-5PM PST
  </div>
  <div class="hero__panel">
    <h1 class="hero__title">Attract More<br>Customers</h1>
    <p class="hero__sub">who spend more money with your<br>business more often!</p>
    <p class="hero__note">Using Free Vacation &amp; Cruise Certificates And Other<br>Incentives Without Breaking The Bank!</p>
    <a class="btn" href="#">Download Free Samples Of Our Incentives</a>
  </div>
</header>

<section class="section imagine">
  <h2 class="heading">Imagine</h2>
  <div class="imagine__card">
    <p>Being able to create exciting give away promotions that will boost your sales without ever having to worry about cost.</p>
    <p>Brightlane Promo Group, Inc. provides high-perceived value promotional incentives to businesses that want to advertise an exciting Give Away that will instantly attract more customers from your existing advertising efforts.</p>
    <p>Your business can give away incentive certificates that are redeemable for luxury hotel &amp; resort stays with airfare included, cruises, cash for gas, groceries, dining and even electronic goods.</p>
  </div>
  <div class="imagine__art" role="img" aria-label="Red horseshoe magnet attracting silver balls"></div>
  <a class="btn" href="#">Download Free Samples Of Our Incentives</a>
</section>

<section class="section how" role="img" aria-label="Tropical beach with palm trees and a hut, tinted blue">
  <h2 class="how__title">How Can We Do It?</h2>
  <p class="how__text" style="top:120px">We help fill empty rooms for thousands of hotels and resorts in hundreds of destinations around the world as well as the major cruise lines. Hotels and resorts are rarely full so when we place someone in their empty rooms, they end up making it up when travelers spend money on room service, spa services, eat at their in-house restaurants, casino and take advantage of other amenities that drive revenue.</p>
  <p class="how__text" style="top:230px;left:294px;width:612px">We also help over 18,000 restaurants, electronic manufacturers, the major gas companies and top grocery chains in the U.S and Canada increase brand awareness as well as increase customer loyalty.</p>
  <a class="btn btn--center" href="#">Download Free Samples Of Our Incentives</a>
</section>

<section class="section why">
  <h2 class="heading">Why Offer Incentives<br>To Customers?</h2>

  <div class="benefit" style="left:192px">
    <div class="benefit__ring"><svg width="62" height="52" viewBox="0 0 62 52" fill="none" stroke="var(--blue)" stroke-width="3"><path d="M4 2v46h56"/><rect x="14" y="30" width="7" height="16" fill="var(--blue)"/><rect x="26" y="24" width="7" height="22" fill="var(--blue)"/><rect x="38" y="28" width="7" height="18" fill="var(--blue)"/><rect x="50" y="16" width="7" height="30" fill="var(--blue)"/><path d="M12 24l12-12 10 8 18-16"/></svg></div>
    <p class="benefit__label">Increase Responses<br>From Your Existing Ads</p>
  </div>
  <div class="benefit" style="left:353px">
    <div class="benefit__ring"><svg width="62" height="56" viewBox="0 0 62 56" fill="none" stroke="var(--blue)" stroke-width="5"><circle cx="22" cy="20" r="10" stroke-dasharray="5 3"/><circle cx="22" cy="20" r="4" stroke-width="3"/><circle cx="44" cy="38" r="8" stroke-dasharray="4 3"/><circle cx="44" cy="38" r="3" stroke-width="3"/></svg></div>
    <p class="benefit__label">#1 Sales Closing Tool -<br>Gift w/ Purchase</p>
  </div>
  <div class="benefit" style="left:514px">
    <div class="benefit__ring"><svg width="50" height="64" viewBox="0 0 50 64"><path d="M14 34l-8 26 10-5 6 8 4-22zM36 34l8 26-10-5-6 8-4-22z" fill="var(--blue)"/><circle cx="25" cy="22" r="19" fill="var(--blue)"/><circle cx="25" cy="22" r="12" fill="#fff"/><path d="M25 14l2.5 5 5.5.8-4 3.9 1 5.5-5-2.6-5 2.6 1-5.5-4-3.9 5.5-.8z" fill="var(--blue)"/></svg></div>
    <p class="benefit__label">Build Brand<br>Awareness and Trust</p>
  </div>
  <div class="benefit" style="left:682px">
    <div class="benefit__ring"><svg width="60" height="56" viewBox="0 0 60 56"><path d="M30 4l12 5v10c0 8-5 13-12 16-7-3-12-8-12-16V9z" fill="var(--blue)"/><path d="M24 19l5 5 8-9" stroke="#fff" stroke-width="3" fill="none"/><path d="M4 28v18l12 8h10V44l-8-6-4-10zM56 28v18l-12 8H34V44l8-6 4-10z" fill="var(--blue)"/></svg></div>
    <p class="benefit__label">Insure The Sale Over<br>Your Competition</p>
  </div>
  <div class="benefit" style="left:849px">
    <div class="benefit__ring"><svg width="66" height="44" viewBox="0 0 66 44"><path d="M2 8h12v22H2zM52 8h12v22H52z" fill="var(--blue)"/><path d="M14 10l12-4 10 4 8-2 8 2v18l-16 12c-2 2-5 2-7 0L14 28z" fill="var(--blue)"/><path d="M26 12l-6 8c2 2 5 2 7 0l5-4" stroke="#fff" stroke-width="2.5" fill="none"/></svg></div>
    <p class="benefit__label">Boost Repeat and<br>Referral Business-</p>
  </div>
  <div class="benefit" style="left:1010px">
    <div class="benefit__ring"><svg width="60" height="60" viewBox="0 0 60 60" fill="none" stroke="var(--blue)" stroke-width="4"><path d="M48 18A22 22 0 0012 16"/><path d="M12 42a22 22 0 0036 2"/><path d="M44 10l4 8-8 2M16 50l-4-8 8-2"/><text x="30" y="39" text-anchor="middle" font-family="Lato,Arial,sans-serif" font-weight="900" font-size="24" fill="var(--blue)" stroke="none">$</text></svg></div>
    <p class="benefit__label">Improve<br>Retention Rates</p>
  </div>

  <a class="btn btn--center" href="#">Download Free Samples Of Our Incentives</a>
</section>

<section class="section testimonials">
  <h2 class="heading">Testimonials</h2>
  <span class="quote__mark" style="left:290px;top:118px">&ldquo;</span>
  <p class="quote">I began using your incentives two years ago to boost lead generation efforts. I have experienced a 63% increase in lead captures. And, even more importantly, my sales have increased as well. The ability to offer unlimited certificates and not having to pay for each certificate I give away is perhaps the best feature of the program, but having the flexibility to email or print certificates for my customers is also wonderful. I even use your html banners to automate my promotions right on my website!</p>
  <span class="quote__mark" style="left:800px;top:300px">&rdquo;</span>
  <p class="quote__name">Dan R.</p>
  <p class="quote__place">Oakridge, TN</p>
  <a class="btn btn--center" href="#">Download Free Samples Of Our Incentives</a>
</section>

<footer class="section footer">© 2017 Brightlane Promo Group, Inc. - All Rights Reserved</footer>

</body>
</html>
```